Card Design for my dog training business Brightpaw Obedience

Need a business card design for my dog training business with my new logo. Want the card to come off professional yet fun. Want it to be very eye catchy as well. I normally have these at vet clinics, pet stores, and groomers. so need it to look better than my competitors.
Target Market(s)
dog owners
Industry/Entity Type
Dog Training
Contact Information for Business Card
needs logo, my name and info
Font styles to use
Serif
Colors
0255a3
ffffff
ec1f27
000000
333333
fbfbfb
Requirements
Must have
- Brightpaw Obedience
- Felix Orland
- 415 903 2276
- info@brightpawobedience.example
- www.brightpawobedience.example

```html
<!DOCTYPE html>
<html lang="en">
<head>
<meta charset="utf-8">
<title>Brightpaw Obedience – Business Card</title>
<link href="https://fonts.googleapis.com/css2?family=Libre+Baskerville:ital,wght@0,400;0,700;1,400&display=swap" rel="stylesheet">
<style>
  :root {
    --ink: #000000;
    --paper: #fbfbfb;
    --white: #ffffff;
    --stage: #e6e4e4;
    --rule: #d9d9d9;
  }
  * { box-sizing: border-box; margin: 0; padding: 0; }
  html, body { width: 1200px; height: 862px; overflow: hidden; }
  body {
    background: var(--stage);
    display: flex;
    align-items: center;
    justify-content: center;
    gap: 90px;
    font-family: "Libre Baskerville", Georgia, serif;
  }
  .card {
    width: 330px;
    height: 576px;
    position: relative;
    box-shadow: 0 10px 30px rgba(0,0,0,0.18);
  }
  /* Front */
  .card--front { background: var(--ink); }
  .card__panel {
    position: absolute;
    inset: 18px;
    background: var(--paper);
    clip-path: polygon(26px 0, calc(100% - 26px) 0, calc(100% - 26px) 26px, 100% 26px,
                       100% calc(100% - 26px), calc(100% - 26px) calc(100% - 26px), calc(100% - 26px) 100%,
                       26px 100%, 26px calc(100% - 26px), 0 calc(100% - 26px), 0 26px, 26px 26px);
    display: flex;
    flex-direction: column;
    align-items: center;
    justify-content: center;
    text-align: center;
    padding: 0 16px;
  }
  .brand-name {
    font-weight: 700;
    font-size: 26px;
    line-height: 1.2;
    letter-spacing: 0.04em;
    text-transform: uppercase;
  }
  .brand-name--dark { color: var(--ink); }
  .brand-name--light { color: var(--white); }
  .tagline {
    margin-top: 22px;
    font-style: italic;
    font-size: 10.5px;
    white-space: nowrap;
    color: var(--ink);
  }
  /* Back */
  .card--back {
    background: var(--ink);
    color: var(--white);
    display: flex;
    flex-direction: column;
    align-items: center;
    padding: 120px 34px 0;
    text-align: center;
  }
  .card__name-block {
    margin-top: 70px;
    width: 100%;
    border-top: 1px solid var(--rule);
    border-bottom: 1px solid var(--rule);
    padding: 14px 0;
  }
  .card__name {
    font-weight: 700;
    font-size: 19px;
    letter-spacing: 0.03em;
    text-transform: uppercase;
  }
  .contact {
    list-style: none;
    margin-top: 40px;
    font-size: 13.5px;
    line-height: 1.55;
    white-space: nowrap;
  }
</style>
</head>
<body>
  <section class="card card--front">
    <div class="card__panel">
      <div class="brand-name brand-name--dark">Brightpaw<br>Obedience</div>
      <p class="tagline">“Good habits start with one patient lesson.”</p>
    </div>
  </section>

  <section class="card card--back">
    <div class="brand-name brand-name--light">Brightpaw<br>Obedience</div>
    <div class="card__name-block">
      <h1 class="card__name">Felix Orland</h1>
    </div>
    <ul class="contact">
      <li>415 903 2276</li>
      <li>info@brightpawobedience.example</li>
      <li>www.brightpawobedience.example</li>
    </ul>
  </section>
</body>
</html>
```